Business card for medical clinic

I need an upmarket, modern medical/health business card for my clinic

Contact Information for Business Card

name, address, email, qr code

```html
<!DOCTYPE html>
<html lang="en">
<head>
<meta charset="utf-8">
<title>Calder Health Partners – Business Card</title>
<link href="https://fonts.googleapis.com/css2?family=Montserrat:wght@400;500;700;800&display=swap" rel="stylesheet">
<style>
  :root {
    --backdrop: #262626;
    --card: #ffffff;
    --navy: #1b3358;
    --blue: #1c73b0;
    --sky: #2aa6e0;
    --ink: #222428;
    --shadow: rgba(0, 0, 0, 0.45);
  }
  * { box-sizing: border-box; margin: 0; padding: 0; }
  html, body {
    width: 1200px;
    height: 880px;
    overflow: hidden;
    background: var(--backdrop);
    font-family: "Montserrat", Arial, sans-serif;
  }
  .canvas { position: relative; width: 1200px; height: 880px; }
  .card {
    position: absolute;
    width: 620px;
    height: 354px;
    background: var(--card);
    border-radius: 26px;
    box-shadow: 0 10px 28px var(--shadow);
    overflow: hidden;
  }
  .card--front { left: 70px; top: 70px; }
  .card--back { left: 510px; top: 456px; }

  .brand {
    position: absolute;
    display: flex;
    align-items: center;
    gap: 14px;
    color: var(--navy);
    font-weight: 700;
    letter-spacing: 0.05em;
    white-space: nowrap;
  }
  .brand__dot {
    flex: none;
    border-radius: 50%;
    background: var(--blue);
  }
  .card--front .brand {
    left: 0;
    right: 0;
    top: 150px;
    justify-content: center;
    font-size: 26px;
  }
  .card--front .brand__dot { width: 36px; height: 36px; }
  .card--back .brand { right: 30px; top: 62px; font-size: 18px; gap: 12px; }
  .card--back .brand__dot { width: 24px; height: 24px; }

  .person { position: absolute; left: 70px; top: 160px; }
  .person__name {
    color: var(--blue);
    font-weight: 800;
    font-size: 25px;
    letter-spacing: 0.02em;
    line-height: 1.1;
  }
  .person__role {
    color: var(--ink);
    font-weight: 400;
    font-size: 16px;
    margin-top: 2px;
  }
  .accent-bar {
    position: absolute;
    left: 40px;
    top: 166px;
    width: 16px;
    height: 54px;
    background: linear-gradient(180deg, var(--navy), var(--sky));
  }
  .divider {
    position: absolute;
    left: 70px;
    right: 38px;
    top: 232px;
    height: 2px;
    background: var(--blue);
  }
  .address {
    position: absolute;
    right: 40px;
    top: 168px;
    text-align: right;
    color: var(--ink);
    font-size: 15px;
    line-height: 1.45;
  }
  .contacts {
    position: absolute;
    left: 70px;
    top: 248px;
    list-style: none;
    color: var(--ink);
    font-size: 16px;
  }
  .contacts li {
    display: flex;
    align-items: center;
    gap: 10px;
    height: 28px;
  }
  .contacts svg { width: 16px; height: 16px; flex: none; }
</style>
</head>
<body>
<main class="canvas">

  <section class="card card--front" aria-label="Card front">
    <div class="brand"><span class="brand__dot"></span>CALDER HEALTH PARTNERS</div>
  </section>

  <section class="card card--back" aria-label="Card back">
    <div class="brand"><span class="brand__dot"></span>CALDER HEALTH PARTNERS</div>

    <span class="accent-bar"></span>
    <div class="person">
      <h1 class="person__name">DANIEL HAYES</h1>
      <p class="person__role">Managing Director</p>
    </div>

    <p class="address">Your address, City<br>State, Zip 1234</p>

    <span class="divider"></span>

    <ul class="contacts">
      <li>
        <svg viewBox="0 0 16 16" aria-hidden="true"><path fill="var(--blue)" d="M3.6 1.2l2.3 2.6-1.4 1.8c.9 2 2.5 3.6 4.5 4.5l1.8-1.4 2.6 2.3-1.3 2.4C6.4 13.8 2.2 9.6 1.6 3.9z"/></svg>
        555 204 318
      </li>
      <li>
        <svg viewBox="0 0 16 16" aria-hidden="true"><rect x="1" y="3" width="14" height="10" rx="1.5" fill="var(--blue)"/><path d="M1.5 4l6.5 5 6.5-5" fill="none" stroke="#fff" stroke-width="1.3"/></svg>
        info@calderhealth.com
      </li>
      <li>
        <svg viewBox="0 0 16 16" aria-hidden="true"><circle cx="8" cy="8" r="7" fill="var(--blue)"/><path d="M1 8h14M8 1c-3 3.5-3 10.5 0 14M8 1c3 3.5 3 10.5 0 14" fill="none" stroke="#fff" stroke-width="1"/></svg>
        www.calderhealth.com
      </li>
    </ul>
  </section>

</main>
</body>
</html>
```